Bramwell Lodge Business Cards design with a logo

I want two Business cards designed with a very modern contemporary logo UNING 1920'S FONT STYLES with the following details

Address:
Bramwell Lodge
17 Pellham Road
Helensburgh
G83 2RN

Details for card 1

Name: Dermot Ashby
email: Dermot.ashby@bramwell.lodge
Tel : +971 52 318 6094
Tel +44 7700 900 318

Details Card 2

Name: Dermot Ashby
email: Neville.osgood@bramwell.lodge
Tel : +971 52 430 9187

Bramwell lodge is a house that was built around 1880 and was used extensively in the 1920's for entertaining and parties in the arts scene, the house again will be resurrected to a modern entertainment venue

If you have any questions feel free to ask

Target Market(s)

The market for this is the young modern crowd

Industry/Entity Type

Entertainment Industry

Contact Information for Business Card

Address:
Bramwell Lodge
17 Pellham Road
Helensburgh
G83 2RN

Details for card 1

Name: Dermot Ashby
Tel : +971 52 318 6094
Tel +44 7700 900 318

Details Card 2

Name: Neville Osgood
Tel : +971 52 430 9187

Logo Text

Bramwell Lodge

Font styles to use
Other font styles liked:
• 1920'S FONT STULES

Requirements
Must have
• Modern Contemporary, whilst taking into consideration the age of the house as detailed above. YOU MUT BE USING 1920'S FONT STYLES
Nice to have
• 1920'S FONT STYLES see attached image if a suggestion
Should not have
• Should not look old or dated

```html
<!DOCTYPE html>
<html lang="en">
<head>
<meta charset="utf-8">
<title>Bramwell Lodge — Business Cards</title>
<link rel="stylesheet" href="https://fonts.googleapis.com/css2?family=Federo&family=Montserrat:wght@500&family=Poiret+One&display=swap">
<style>
  :root {
    --backdrop: #262627;
    --card: #1b1b1c;
    --card-edge: #2c2c2d;
    --silver: #d9d9d9;
    --silver-dim: #9a9a9a;
    --emboss: #0f0f10;
    --emboss-light: #3a3a3b;
    --rule: #6e6e6e;
  }
  * { box-sizing: border-box; margin: 0; padding: 0; }
  html, body {
    width: 1200px; height: 900px; overflow: hidden;
    background: var(--backdrop);
  }
  .sheet {
    width: 1200px; height: 900px;
    display: flex; flex-direction: column; align-items: center; justify-content: center;
    gap: 34px;
  }
  .card {
    position: relative;
    width: 640px; height: 366px;
    background: radial-gradient(ellipse at 70% 40%, #242425 0%, var(--card) 70%);
    border: 1px solid var(--card-edge);
    box-shadow: 0 14px 30px rgba(0,0,0,.55);
  }
  /* front */
  .brand-name {
    position: absolute; left: 0; right: 0; top: 132px;
    text-align: center;
    font-family: "Montserrat", sans-serif; font-weight: 500;
    font-size: 54px; letter-spacing: 1px;
    color: var(--silver);
  }
  .front-web {
    position: absolute; left: 0; right: 0; bottom: 28px;
    text-align: center;
    font-family: "Federo", sans-serif; font-size: 14px; letter-spacing: 1px;
    color: var(--silver-dim);
  }
  /* back */
  .holder {
    position: absolute; right: 352px; top: 112px;
    text-align: right;
  }
  .holder-name {
    font-family: "Poiret One", sans-serif; font-size: 28px; font-weight: 400;
    letter-spacing: 1px; text-transform: uppercase;
    color: var(--emboss);
    text-shadow: 0 1px 0 var(--emboss-light), 0 -1px 0 #000;
  }
  .holder-role {
    margin-top: 4px;
    font-family: "Federo", sans-serif; font-size: 13px; letter-spacing: 1px;
    color: var(--emboss);
    text-shadow: 0 1px 0 var(--emboss-light);
  }
  .divider {
    position: absolute; left: 306px; top: 104px;
    width: 1px; height: 92px; background: var(--rule);
  }
  .contacts {
    position: absolute; left: 330px; top: 106px;
    list-style: none;
  }
  .contacts li {
    display: flex; align-items: center; gap: 12px;
    height: 21px;
    font-family: "Federo", sans-serif; font-size: 15px; letter-spacing: .6px;
    color: var(--silver);
  }
  .contacts svg { width: 11px; height: 11px; flex: none; }
  .address {
    position: absolute; left: 28px; bottom: 40px;
    display: flex; align-items: center; gap: 12px;
    font-family: "Federo", sans-serif; font-size: 17px; letter-spacing: .8px;
    color: var(--emboss);
    text-shadow: 0 1px 0 var(--emboss-light);
  }
  .address-mark {
    width: 16px; height: 16px; background: var(--emboss);
    box-shadow: 0 1px 0 var(--emboss-light);
  }
  .address-postcode { color: var(--silver); text-shadow: none; margin-left: 10px; }
</style>
</head>
<body>
<main class="sheet">
  <section class="card card-front">
    <h1 class="brand-name">Bramwell Lodge</h1>
    <p class="front-web">www.bramwelllodge.com</p>
  </section>

  <section class="card card-back">
    <div class="holder">
      <h2 class="holder-name">Dermot Ashby</h2>
      <p class="holder-role">Director</p>
    </div>
    <div class="divider"></div>
    <ul class="contacts">
      <li>
        <svg viewBox="0 0 12 12" aria-hidden="true"><path d="M2 1h2.5l1 3-1.5 1a6 6 0 0 0 3 3l1-1.5 3 1V10a1 1 0 0 1-1 1A9 9 0 0 1 1 2a1 1 0 0 1 1-1z" fill="none" stroke="#d9d9d9" stroke-width="1"/></svg>
        +971 52 318 6094
      </li>
      <li>
        <svg viewBox="0 0 12 12" aria-hidden="true"><path d="M1 4c2-2.5 8-2.5 10 0l-1.5 1.2L8 4.5V3.5H4v1l-1.5.7z" fill="#d9d9d9"/><rect x="2.5" y="6" width="7" height="4.5" rx="1" fill="#d9d9d9"/></svg>
        +44 7700 900 318
      </li>
      <li>
        <svg viewBox="0 0 12 12" aria-hidden="true"><rect x="1" y="2.5" width="10" height="7" fill="none" stroke="#d9d9d9"/><path d="M1 2.5l5 4 5-4" fill="none" stroke="#d9d9d9"/></svg>
        Dermot.ashby@bramwell.lodge
      </li>
      <li>
        <svg viewBox="0 0 12 12" aria-hidden="true"><circle cx="6" cy="6" r="5" fill="none" stroke="#d9d9d9"/><ellipse cx="6" cy="6" rx="2.2" ry="5" fill="none" stroke="#d9d9d9"/><path d="M1 6h10" stroke="#d9d9d9"/></svg>
        www.bramwelllodge.com
      </li>
    </ul>
    <p class="address">
      <span class="address-mark"></span>
      Bramwell Lodge, 17 Pellham Road Helensburgh
      <span class="address-postcode">G83 2RN</span>
    </p>
  </section>
</main>
</body>
</html>
```